Kelvor Engineers: Why you should hire us keepsake

New design. Open to plastic cards. We are an engineering firm that designs cell phone towers and commercial buildings. Please check out our website www.kelvorstruct.com for more details. We want people to remember our card and for it to be useful if possible. We want the same look and feel on these cards to be translated to other marketing material we may need such as brochures.

Target Market(s)

Architects, Developers and Telecommunication Carriers

Industry/Entity Type

Engineering

Contact Information for Business Card

Card with our company colors, logo, and innovative design with elements related to our industry.

Font styles to use
Sans Serif

Colors
9bcb3c
abd036
0255a3

Requirements
Must have
• Sleek and hip design
Nice to have
• Bright lime green and navy coloring that pops with an innovative design.
Should not have
• A basic and boring design

```html
<!DOCTYPE html>
<html lang="en">
<head>
<meta charset="UTF-8">
<title>Kelvor Engineers – Business Card</title>
<link rel="stylesheet" href="https://fonts.googleapis.com/css2?family=Roboto+Condensed:wght@700&family=Roboto:wght@400&display=swap">
<style>
  :root {
    --backdrop: #2b2b2b;
    --card-white: #f3f3f3;
    --navy: #032b5a;
    --navy-line: #0a2f5c;
    --lime: #27f01a;
    --grey-text: #4a4a4a;
    --white-text: #ffffff;
    --pattern-tone: #2e5986;
  }
  html, body {
    margin: 0;
    padding: 0;
    width: 1200px;
    height: 960px;
    overflow: hidden;
    background: var(--backdrop);
  }
  .canvas {
    position: relative;
    width: 1200px;
    height: 960px;
  }
  .card {
    position: absolute;
    left: 320px;
    width: 600px;
    border-radius: 22px;
    overflow: hidden;
  }
  .card-front {
    top: 100px;
    height: 350px;
    background: var(--card-white);
  }
  .card-back {
    top: 493px;
    height: 342px;
    background: var(--navy);
  }
  .brand-name {
    position: absolute;
    top: 140px;
    left: 0;
    right: 0;
    text-align: center;
    margin: 0;
    font-family: "Roboto Condensed", sans-serif;
    font-weight: 700;
    font-size: 66px;
    line-height: 1;
    color: var(--lime);
    letter-spacing: 0.5px;
  }
  .tagline {
    position: absolute;
    top: 274px;
    left: 0;
    right: 0;
    display: flex;
    justify-content: center;
    align-items: center;
    gap: 3px;
    font-family: "Roboto Condensed", sans-serif;
    font-weight: 700;
    font-size: 16.5px;
    color: var(--lime);
    letter-spacing: 0.6px;
  }
  .tagline::before,
  .tagline::after {
    content: "";
    width: 30px;
    height: 2px;
    background: var(--navy-line);
  }
  .offices {
    position: absolute;
    top: 296px;
    left: 0;
    right: 0;
    text-align: center;
    font-family: "Roboto", sans-serif;
    font-size: 15px;
    color: var(--grey-text);
    letter-spacing: 0.9px;
  }
  .pattern-field {
    position: absolute;
    left: 0;
    top: 0;
  }
  .contact-block {
    position: absolute;
    left: 337px;
    top: 182px;
  }
  .person-name {
    margin: 0 0 12px;
    font-family: "Roboto Condensed", sans-serif;
    font-weight: 700;
    font-size: 21px;
    color: var(--lime);
    letter-spacing: 0px;
  }
  .contact-list {
    list-style: none;
    margin: 0;
    padding: 0;
  }
  .contact-list li {
    display: flex;
    align-items: center;
    gap: 9px;
    height: 19px;
    font-family: "Roboto", sans-serif;
    font-size: 14.5px;
    color: var(--white-text);
  }
  .contact-icon {
    width: 14px;
    height: 14px;
    flex: none;
  }
</style>
</head>
<body>
<div class="canvas">

  <section class="card card-front">
    <h1 class="brand-name">Kelvor Engineers</h1>
    <div class="tagline">MULTI-DISCIPLINE ENGINEERING</div>
    <div class="offices">Brookmere | Dalton Ridge | Ferris Bay | Oak Hollow</div>
  </section>

  <section class="card card-back">
    <svg class="pattern-field" width="600" height="342" viewBox="0 0 600 342" role="img" aria-label="Stepped checkerboard pattern in navy and slate blue along the top-left corner">
      <polygon fill="var(--pattern-tone)" opacity="0.55"
        points="0,0 440,0 440,48 392,48 392,98 342,98 342,148 293,148 293,198 245,198 245,248 196,248 196,298 147,298 147,342 0,342"/>
    </svg>

    <div class="contact-block">
      <h2 class="person-name">DANA HOLLOWAY PRYCE</h2>
      <ul class="contact-list">
        <li>
          <svg class="contact-icon" viewBox="0 0 24 24"><path fill="var(--lime)" d="M6.6 10.8a15.1 15.1 0 0 0 6.6 6.6l2.2-2.2c.3-.3.7-.4 1-.2 1.1.4 2.3.6 3.6.6.6 0 1 .4 1 1V20c0 .6-.4 1-1 1C10.6 21 3 13.4 3 4c0-.6.4-1 1-1h3.5c.6 0 1 .4 1 1 0 1.3.2 2.5.6 3.6.1.3 0 .7-.2 1z"/></svg>
          555.214.7730
        </li>
        <li>
          <svg class="contact-icon" viewBox="0 0 24 24"><rect x="6" y="1" width="12" height="22" rx="2" fill="var(--lime)"/><rect x="8" y="4" width="8" height="14" fill="var(--navy)"/><circle cx="12" cy="20.5" r="1.2" fill="var(--navy)"/></svg>
          555.381.6042
        </li>
        <li>
          <svg class="contact-icon" viewBox="0 0 24 24"><rect x="2" y="5" width="20" height="14" rx="1.5" fill="var(--lime)"/><path d="M2.5 6l9.5 7 9.5-7" fill="none" stroke="var(--navy)" stroke-width="2"/></svg>
          dpryce@kelvorstruct.com
        </li>
        <li>
          <svg class="contact-icon" viewBox="0 0 24 24"><circle cx="12" cy="12" r="10" fill="var(--lime)"/><path d="M12 2v20M2 12h20M12 2c-3.5 3-3.5 17 0 20M12 2c3.5 3 3.5 17 0 20" fill="none" stroke="var(--navy)" stroke-width="1.4"/></svg>
          www.kelvorstruct.com
        </li>
      </ul>
    </div>
  </section>

</div>
</body>
</html>
```